Brightwave Reach - Business Card

We need a business card for a Social Media Marketing company that specializes in online marketing for small businesses in Canada using common Social Media platforms such as Pixlora, Chatterly, Blinkpost & Quibber.

I have uploaded a copy of our logo which I would like utilized in the business card. We would like the business card to be modern yet classy design.

Our website is www.brightwavereach.ca

Industry/Entity Type

Marketing

Contact Information for Business Card

Email: info@brightwavereach.ca
Website: www.brightwavereach.ca
Telephone: 604-555-0193

Colors

Designer to choose colors to be used in the design.

Requirements
Must have
• Social Media icons on reverse
• Please add some designs with color.

```html
<!DOCTYPE html>
<html lang="en">
<head>
<meta charset="utf-8">
<title>Brightwave Reach – Business Card</title>
<link rel="stylesheet" href="https://fonts.googleapis.com/css2?family=Open+Sans:wght@400;700;800&display=swap">
<style>
  :root {
    --page: #2b2b2c;
    --card: #f2f2f2;
    --card-shade: #e6e6e6;
    --panel: #3b3e3f;
    --ink: #3a3a3a;
    --white: #ffffff;
    --muted: #d9dbdc;
    --rule: #5a5a5a;
  }
  * { box-sizing: border-box; margin: 0; padding: 0; }
  html, body { width: 1200px; height: 960px; overflow: hidden; }
  body {
    background: var(--page);
    font-family: "Open Sans", Arial, sans-serif;
    position: relative;
  }
  .card {
    position: absolute;
    left: 240px;
    width: 720px;
    height: 410px;
    background: linear-gradient(135deg, var(--white), var(--card) 55%, var(--card-shade));
    overflow: hidden;
  }
  .card--back { top: 50px; }
  .card--front { top: 500px; display: flex; }

  /* Back */
  .back-mark {
    position: absolute;
    top: 120px; left: 0; right: 0;
    text-align: center;
    font-weight: 800;
    font-size: 40px;
    letter-spacing: 1px;
    text-transform: uppercase;
    color: var(--ink);
  }
  .social-row {
    position: absolute;
    top: 300px; left: 40px; right: 40px;
    display: flex; align-items: center; gap: 14px;
  }
  .social-row .rule { flex: 1; height: 1px; background: var(--rule); }
  .social {
    display: flex; align-items: center; gap: 6px;
    font-size: 13px; font-weight: 700; color: var(--ink);
  }
  .social .dot {
    width: 22px; height: 22px; border-radius: 50%;
    border: 2px solid var(--ink);
  }

  /* Front */
  .info-panel {
    width: 270px;
    height: 100%;
    background: var(--panel);
    color: var(--white);
    padding: 80px 0 0 34px;
  }
  .divider {
    width: 14px; height: 100%;
    background: var(--white);
    border-right: 8px solid var(--panel);
  }
  .person-name { font-weight: 700; font-size: 19px; letter-spacing: .5px; }
  .person-title { font-size: 15px; color: var(--muted); margin-top: 2px; }
  .contacts { list-style: none; margin-top: 38px; }
  .contacts li {
    display: flex; align-items: center; gap: 10px;
    font-size: 15px; color: var(--muted); margin-bottom: 6px;
  }
  .contacts svg { width: 14px; height: 14px; fill: var(--muted); flex: none; }
  .logo-area {
    flex: 1;
    display: flex; align-items: center; justify-content: center; gap: 14px;
  }
  .logo-square {
    width: 26px; height: 26px;
    border: 4px solid var(--ink);
  }
  .logo-name {
    font-weight: 800; font-size: 36px; line-height: 1.05;
    text-transform: uppercase; color: var(--ink);
  }
</style>
</head>
<body>

<section class="card card--back" aria-label="Business card, back">
  <div class="back-mark">Brightwave Reach</div>
  <div class="social-row">
    <span class="rule"></span>
    <span class="social"><span class="dot"></span>Chatterly</span>
    <span class="social"><span class="dot"></span>Pixlora</span>
    <span class="social"><span class="dot"></span>Quibber</span>
    <span class="rule"></span>
  </div>
</section>

<section class="card card--front" aria-label="Business card, front">
  <div class="info-panel">
    <p class="person-name">DANIEL HART</p>
    <p class="person-title">CEO/FOUNDER</p>
    <ul class="contacts">
      <li>
        <svg viewBox="0 0 24 24" aria-hidden="true"><path d="M6.6 10.8a15.1 15.1 0 0 0 6.6 6.6l2.2-2.2a1 1 0 0 1 1-.25 11.4 11.4 0 0 0 3.6.57 1 1 0 0 1 1 1V20a1 1 0 0 1-1 1A17 17 0 0 1 3 4a1 1 0 0 1 1-1h3.5a1 1 0 0 1 1 1c0 1.25.2 2.46.57 3.6a1 1 0 0 1-.25 1z"/></svg>
        604-555-0193
      </li>
      <li>
        <svg viewBox="0 0 24 24" aria-hidden="true"><path d="M2 5h20v14H2z M2 5l10 8 10-8" /></svg>
        info@brightwavereach.ca
      </li>
      <li>
        <svg viewBox="0 0 24 24" aria-hidden="true"><circle cx="12" cy="12" r="10"/></svg>
        www.brightwavereach.ca
      </li>
    </ul>
  </div>
  <div class="divider"></div>
  <div class="logo-area">
    <span class="logo-square"></span>
    <span class="logo-name">Brightwave<br>Reach</span>
  </div>
</section>

</body>
</html>
```